Wordpress Theme for Cedarline Clinics

** Please view updated Sitemap2.pdf doc to clarify some confusion ***

This is a multiuser WordPress subscription site for Cedarline Clinics. Please see attachment for sitemap. Please do not include extra content like social media icons, search bars, or images. If you have questions, please ask for clarification.
The site contains the following pages and sub-pages:

1. Home
2. Our Clinic
2a. Our Clinic > Mission
2b. Our Clinic > Services
2c. Our Clinic > Clinic Policies
2d. Our Clinic > Schedules
3. Our Staff
3a. Our Staff > [Staff member page]
4. Resources
4a. Resources > Patient Health (index)
4b. Resources > Patient Health (index) > [post]
4c. Resources > Links
4d. Resources > Forms
5. Alerts
5a. Alerts > [Alert Page]
6. Contact Us

Includes the Following Pages, Subpages, and Content
1. Home
a. About Us
b. Our Staff
c. Bulletins
d. Accepting New Patients (shown as an alert widget)
e. Links
i. Physician Toolbox
ii. Book an Appointment
f. Clinic Policies
i. Show first 3 policies (e.g. Late Arrivals, Missed Appointments, Fees)
ii. Link to Clinic Policies page
g. Primary widget (displayed on all pages)
i. Hours of operation
ii. Contact Info
1. Tel
2. Fax
3. Email
4. Address
5. Get directions (link to Google Maps)
2. Our Clinic
a. Main Page
i. Clinic Name
ii. Overview
iii. Languages Spoken
iv. Secondary Navigation
1. Mission
2. Services
3. Clinic Policies
4. Schedules (see attachment)
b. Our Clinic > Mission
c. Our Clinic > Services
i. For each service include service TITLE and DESCRIPTION
d. Our Clinic > Clinic Policies
i. For each policy include policy TITLE and DESCRIPTION
ii. Include the following policies in mockup
1. Late arrivals
2. Missed appointments
3. Fees for missed appointments
4. Referrals and follow-ups
5. Services not covered by RDA
6. Information for LTF patients
7. Medical Legal Reports
e. Our Clinic > Schedules
3. Our Staff
a. Main Page
i. Display a list of staff members. Include NAME and DESIGNATION
b. Our Staff > [Staff Name]
i. Include NAME, PICTURE, DESIGNATION, and BIO
4. Resources
a. Resources > Patient Health
i. Main Page
1. Posts (ordered by date)
a. Title
b. Summary
2. Side Navigation
a. Post Categories
ii. Patient Health > [post title]
1. Title
2. Post Category
3. Date
4. Author
5. Summary
6. Body
b. Resources > Links
1. Secondary Navigation - Categories
a. Sample Categories:
i. Local Services
ii. RDA and Drug Coverage
iii. Mental Health Resources
2. Category page
a. Include the following links in the 'Local Services' category
i. Hypertension clinics
ii. Home Care services
iii. Vaccine Clinics
c. Resources > Forms
i. Display a table with form TITLE and CATEGORY
ii. Side Navigation
1. Form Categories
a. Use the following sample Categories
i. Referrals
ii. Insurance
iii. Intake
iv. Discharge
v. Waivers
5. Alerts
a. Main page
i. List of all Alert posts
1. Include post TITLE as a link to the post
ii. Side Navigation
1. Alerts Archive
a. shown as Month + Number of posts
iii. Alerts > [Alert page]
1. Include TITLE, DATE, AUTHOR, BODY
6. Contact Us
a. Map
b. Hours of operation
c. Address
d. Phone number
e. Fax number
e. Fax number
f. Map
g. Email

Design notes:
- fixed width
- responsive (need designs for mobile, tablet, and desktop)
- simple, dark font, white background
- use Font Awesome icons where needed
- user adds own logo

Target Market(s)

Cedarline Clinics

Industry/Entity Type

Medical

Number of Pages Required

5+ page

Font styles to use
Serif
Sans Serif

Requirements
Must have
• Please keep designs very simple.
• Examples:
• https://www.quolbin.com/install
• http://www.ventrohax.com/company/about-us
• http://brindlequota.org/
• http://www.trosk.com/
Should not have
• Minimal or no use of shadows and gradients

```html
<!DOCTYPE html>
<html lang="en">
<head>
<meta charset="utf-8">
<title>Schedule – Cedarline Clinics</title>
<link rel="stylesheet" href="https://fonts.googleapis.com/css2?family=Lato:wght@400;700&family=Raleway:wght@500;600;700&display=swap">
<style>
:root{
  --blue:#0b8de3;
  --blue-dark:#0a77cc;
  --blue-table:#3aaaf2;
  --ink:#222;
  --text:#555;
  --muted:#777;
  --line:#cfcfcf;
  --band:#f6f6f6;
  --row-alt:#f4f4f4;
  --tick:#8a8a8a;
  --footer:#262626;
  --footer-text:#8c8c8c;
  --white:#fff;
}
*{box-sizing:border-box;margin:0;padding:0}
html,body{width:1200px;height:834px;overflow:hidden}
body{position:relative;background:var(--white);font-family:"Lato",sans-serif;color:var(--text)}
a{color:inherit;text-decoration:none}
.topbar{position:absolute;left:0;top:0;width:1200px;height:30px;background:var(--blue);color:var(--white);font-size:9.5px}
.topbar .contact{position:absolute;left:162px;top:10px;display:flex}
.topbar .contact span+span{margin-left:8px;padding-left:8px;border-left:1px solid rgba(255,255,255,.8)}
.topbar .quick{position:absolute;right:161px;top:10px;display:flex}
.topbar .quick a+a{margin-left:6px;padding-left:6px;border-left:1px solid rgba(255,255,255,.8)}
.header{position:absolute;left:0;top:30px;width:1200px;height:83px}
.brand{position:absolute;left:162px;top:22px;display:flex;align-items:center;font-family:"Raleway",sans-serif;font-weight:600;font-size:22px;color:var(--ink)}
.brand .dot{width:22px;height:22px;border-radius:50%;background:var(--blue);margin-right:26px}
.nav{position:absolute;right:161px;top:0;display:flex;height:83px;font-size:11px;color:var(--ink)}
.nav a{display:flex;align-items:center;padding:0 17px}
.nav a.active{background:var(--blue-dark);color:var(--white);padding:0 7px;width:60px;justify-content:center;margin:0 17px 0 0}
.nav a:last-child{padding-right:0}
.page-band{position:absolute;left:0;top:113px;width:1200px;height:59px;background:var(--band)}
.page-band h1{position:absolute;left:162px;top:10px;font-family:"Raleway",sans-serif;font-weight:700;font-size:18px;color:var(--ink)}
.crumbs{position:absolute;left:162px;top:37px;font-size:9px;color:#444}
.subnav{position:absolute;left:162px;top:216px;width:202px}
.subnav h2{font-family:"Raleway",sans-serif;font-weight:500;font-size:14px;color:#444;padding-bottom:5px;border-bottom:1px solid #bbb}
.subnav ul{list-style:none}
.subnav li{width:127px;height:22.5px;border-bottom:1px solid var(--line);font-size:12px;color:#555;padding:4px 0 0 14px}
.subnav li:last-child{border:0;color:var(--blue);font-weight:700}
.schedule{position:absolute;left:387px;top:216px;width:427px}
.schedule h2{font-family:"Raleway",sans-serif;font-weight:700;font-size:15px;color:var(--ink);margin-bottom:9px}
table{width:427px;border-collapse:collapse;border:1px solid #ddd;font-size:10.5px}
th{background:var(--blue-table);color:var(--white);font-size:8px;font-weight:700;height:24px;border-left:1px solid rgba(255,255,255,.45)}
th:first-child{border-left:0}
td{height:22.5px;border-left:1px solid #e2e2e2;text-align:center;width:43px}
td.name{text-align:left;width:127px;padding-left:14px;border-left:0;color:#555}
tr:nth-child(even) td{background:var(--row-alt)}
tr.current td.name{color:var(--blue)}
.tick{width:9px;height:8px;vertical-align:middle}
.widget{position:absolute;left:837px;top:209px;width:202px;height:352px;border:1px solid #d6d6d6}
.widget .head{height:33px;background:var(--blue);color:var(--white);font-family:"Raleway",sans-serif;font-weight:500;font-size:14.5px;text-align:center;line-height:33px}
.widget .intro{margin:9px 14px 0;font-size:8.5px;line-height:13.5px;color:var(--muted)}
.hours{margin:10px 15px 0 14px;font-size:8.5px;color:#333}
.hours div{display:flex;justify-content:space-between;height:18px}
.hours .today{color:var(--blue)}
.holidays{margin:2px 14px 0;font-size:8.5px;color:var(--blue);padding-bottom:10px;border-bottom:2px solid #ddd}
.widget h3{margin:16px 14px 0;font-family:"Raleway",sans-serif;font-weight:500;font-size:13px;color:var(--ink)}
.info{margin:6px 14px 0;font-size:8.5px;color:#333;display:grid;grid-template-columns:81px 1fr;row-gap:3px;line-height:12px}
.footer{position:absolute;left:0;top:607px;width:1200px;height:227px;background:var(--footer);border-top:4px solid var(--blue);color:var(--footer-text)}
.footer .brand{left:162px;top:33px;color:var(--white)}
.footer .brand .dot{background:var(--white)}
.footer .about{position:absolute;left:162px;top:89px;width:210px;font-size:8.5px;line-height:13.5px;color:#ccc}
.fcol{position:absolute;top:32px;font-size:10.5px}
.fcol h4{font-family:"Raleway",sans-serif;font-weight:500;font-size:13.5px;color:#999;margin-bottom:9px}
.fcol li{list-style:none;height:18px}
.fcol li.on{color:#eee}
.fcontact{display:grid;grid-template-columns:81px 1fr;line-height:15px;margin-left:2px}
.bottom{position:absolute;left:0;top:192px;width:1200px;height:35px;border-top:1px solid #444;font-size:10.5px;color:#888}
.bottom .copy{position:absolute;left:162px;top:9px}
.bottom .links{position:absolute;left:463px;top:9px;display:flex;gap:20px}
</style>
</head>
<body>
<div class="topbar">
  <div class="contact"><span>To help Here : 555 010 2233</span><span>Email : hello@cedarline.ca</span></div>
  <div class="quick"><a href="#">Book an Appointment</a><a href="#">Physician Toolbox</a></div>
</div>
<header class="header">
  <div class="brand"><span class="dot"></span>Cedarline Clinics</div>
  <nav class="nav">
    <a href="#">Home</a><a href="#" class="active">Our Clinic</a><a href="#">Newsletter</a><a href="#">Our Staff</a><a href="#">Resources</a><a href="#">Contact Us</a>
  </nav>
</header>
<section class="page-band">
  <h1>Schedule</h1>
  <div class="crumbs">Home / Our Clinic / Schedule</div>
</section>
<aside class="subnav">
  <h2>Our Clinic</h2>
  <ul><li>About</li><li>Misssion</li><li>Services</li><li>Policies</li><li>Schedules</li></ul>
</aside>
<section class="schedule">
  <h2>Schedule</h2>
  <svg width="0" height="0" style="position:absolute"><defs><symbol id="tick" viewBox="0 0 10 8"><path d="M1 4.2 3.8 7 9 1" fill="none" stroke="#8a8a8a" stroke-width="2"/></symbol></defs></svg>
  <table>
    <tr><th></th><th>MON</th><th>TUE</th><th>WED</th><th>THU</th><th>FRI</th><th>SAT</th><th>SUN</th></tr>
    <tr class="current"><td class="name">Dr. Laura Penfield</td><td><svg class="tick"><use href="#tick"/></svg></td><td></td><td><svg class="tick"><use href="#tick"/></svg></td><td><svg class="tick"><use href="#tick"/></svg></td><td><svg class="tick"><use href="#tick"/></svg></td><td></td><td><svg class="tick"><use href="#tick"/></svg></td></tr>
    <tr><td class="name">Dr. Owen Marsh</td><td><svg class="tick"><use href="#tick"/></svg></td><td><svg class="tick"><use href="#tick"/></svg></td><td><svg class="tick"><use href="#tick"/></svg></td><td></td><td><svg class="tick"><use href="#tick"/></svg></td><td><svg class="tick"><use href="#tick"/></svg></td><td></td></tr>
    <tr><td class="name">Dr. Ivan Holtby</td><td><svg class="tick"><use href="#tick"/></svg></td><td></td><td><svg class="tick"><use href="#tick"/></svg></td><td><svg class="tick"><use href="#tick"/></svg></td><td></td><td></td><td></td></tr>
    <tr><td class="name">Dr. Paul Ravelle</td><td></td><td><svg class="tick"><use href="#tick"/></svg></td><td></td><td><svg class="tick"><use href="#tick"/></svg></td><td></td><td></td><td></td></tr>
    <tr><td class="name">Dr. Neil Carrow</td><td><svg class="tick"><use href="#tick"/></svg></td><td><svg class="tick"><use href="#tick"/></svg></td><td><svg class="tick"><use href="#tick"/></svg></td><td></td><td><svg class="tick"><use href="#tick"/></svg></td><td></td><td><svg class="tick"><use href="#tick"/></svg></td></tr>
  </table>
</section>
<aside class="widget">
  <div class="head">Hours of Opration</div>
  <p class="intro">Lorem Ipsum is simply dummy text of the printing and typesetting industry.</p>
  <div class="hours">
    <div class="today"><span>Monday :</span><span>8:00 AM - 6:00 PM</span></div>
    <div><span>Tuesday :</span><span>8:00 AM - 6:00 PM</span></div>
    <div><span>Wednessday :</span><span>8:00 AM - 6:00 PM</span></div>
    <div><span>Thursday :</span><span>8:00 AM - 6:00 PM</span></div>
    <div><span>Friday :</span><span>8:00 AM - 6:00 PM</span></div>
    <div><span>Saturday :</span><span>9:00 AM - 4:00 PM</span></div>
    <div><span>Sunday :</span><span>9:00 AM - 4:00 PM</span></div>
  </div>
  <div class="holidays">Holidays</div>
  <h3>Contact Info</h3>
  <div class="info">
    <span>Telephone :</span><span>555-014-7788</span>
    <span>Email:</span><span>hello@cedarline.ca</span>
    <span>Address:</span><span>48 Alder Row<br>Lakeview,B. Canada,<br>K2P 4RT</span>
  </div>
</aside>
<footer class="footer">
  <div class="brand"><span class="dot"></span>Cedarline Clinics</div>
  <p class="about">Lorem Ipsum is simply dummy text of the printing and typesetting industry. Lorem Ipsum has been the industry's standard dummy text ever since</p>
  <div class="fcol" style="left:461px"><h4>Navigation</h4><ul><li class="on">Home</li><li>Our Clinic</li><li>Newsletter</li><li>Our Staff</li><li>Resources</li></ul></div>
  <div class="fcol" style="left:686px"><h4>Links</h4><ul><li>Help</li><li>Support</li><li>Privacy Policy</li></ul></div>
  <div class="fcol" style="left:836px"><h4>Contact Us</h4>
    <div class="fcontact"><span>Telephone :</span><span>555-014-7788</span><span>Email:</span><span>hello@cedarline.ca</span><span>Address:</span><span>48 Alder Row<br>Lakeview,B. Canada,<br>&nbsp;K2P 4RT</span></div>
  </div>
  <div class="bottom">
    <span class="copy">© 2015 Cedarline Clinics. All Rights Reservsd</span>
    <span class="links"><a href="#">About Us</a><a href="#">Terms of Use</a><a href="#">Privacy Policy</a></span>
  </div>
</footer>
</body>
</html>
```